Harborline Auto LLC

Car Dealer Customer Service
Address: 2874 Cresthaven Road, Shelbyville, TN 37162
web: www.harborlineautoxq.net
email: harborlineautoxq@mailnest.example
Phone: (931) 555-0148
Phone: (629) 555-0173

```html
<!DOCTYPE html>
<html lang="en">
<head>
<meta charset="utf-8">
<title>Harborline Auto – Business Card</title>
<link rel="stylesheet" href="https://fonts.googleapis.com/css2?family=Montserrat:wght@700;800&family=Inter:wght@400;500&display=swap">
<style>
  :root {
    --page-bg: #ece8e3;
    --card-frost: #f3f4f5;
    --brand-blue: #1b5e93;
    --deep-blue: #0f4474;
    --brand-orange: #d98a2b;
    --band-orange: #c9771f;
    --text-light: #e9eef4;
    --text-soft: #c9d6e4;
  }
  * { margin: 0; padding: 0; box-sizing: border-box; }
  html, body { width: 1200px; height: 969px; overflow: hidden; }
  body {
    background: var(--page-bg);
    font-family: "Inter", sans-serif;
    position: relative;
  }
  .card {
    position: absolute;
    left: 100px; top: 200px;
    width: 1000px; height: 570px;
    border-radius: 32px;
    background: linear-gradient(135deg, #fafbfc 0%, var(--card-frost) 60%, #e6e8ea 100%);
    box-shadow: 0 18px 40px rgba(0,0,0,0.18);
    overflow: hidden;
  }
  .accent-band {
    position: absolute;
    left: 768px; top: 0;
    width: 232px; height: 100%;
    background: linear-gradient(180deg, #d98a2b 0%, var(--band-orange) 100%);
  }
  .contact-disc {
    position: absolute;
    left: 418px; top: -6px;
    width: 582px; height: 582px;
    border-radius: 50%;
    background: radial-gradient(circle at 55% 35%, #1d66a6 0%, var(--brand-blue) 40%, var(--deep-blue) 100%);
  }
  .brand {
    position: absolute;
    left: 40px; width: 360px; top: 190px;
    text-align: center;
  }
  .brand-dot {
    width: 110px; height: 110px;
    border-radius: 50%;
    background: var(--brand-orange);
    margin: 0 auto 26px;
  }
  .brand-name {
    font-family: "Montserrat", sans-serif;
    font-weight: 800;
    font-size: 33px;
    letter-spacing: 0.5px;
    color: var(--brand-blue);
  }
  .contact {
    position: absolute;
    left: 530px; width: 360px; top: 88px;
    text-align: center;
    color: var(--text-light);
  }
  .vehicle-art {
    width: 195px; height: 72px;
    margin: 0 auto 22px;
    border-radius: 10px;
    background: linear-gradient(180deg, #e39a3c, #c97a22);
  }
  .person-name {
    font-family: "Montserrat", sans-serif;
    font-weight: 800;
    font-size: 36px;
    color: #efe4d4;
    white-space: nowrap;
  }
  .person-role {
    font-size: 21px;
    color: var(--text-soft);
    margin-top: 2px;
  }
  .divider {
    width: 46px; height: 2px;
    background: var(--brand-orange);
    margin: 12px auto 16px;
  }
  .address { font-size: 21px; line-height: 28px; }
  .icon-row {
    display: flex; justify-content: center; gap: 4px;
    margin: 18px 0 14px;
  }
  .icon-row svg { width: 34px; height: 34px; }
  .phones, .email, .web { font-size: 21px; line-height: 29px; white-space: nowrap; }
  .email { font-size: 18px; }
  .phones .sep { color: var(--brand-orange); margin: 0 6px; }
</style>
</head>
<body>
  <div class="card">
    <div class="accent-band"></div>
    <div class="contact-disc"></div>

    <div class="brand">
      <div class="brand-dot"></div>
      <div class="brand-name">HARBORLINE AUTO</div>
    </div>

    <div class="contact">
      <div class="vehicle-art" role="img" aria-label="Vintage car illustration"></div>
      <div class="person-name">DANIEL PRESCOTT</div>
      <div class="person-role">Founder &amp; CEO</div>
      <div class="divider"></div>
      <div class="address">2874 Cresthaven Road<br>Shelbyville, TN 37162</div>
      <div class="icon-row">
        <svg viewBox="0 0 34 34" aria-hidden="true"><circle cx="17" cy="17" r="16" fill="#d98a2b"/><path d="M11 9c1-1 2-1 3 0l2 3c.6 1 .3 1.8-.5 2.4l-1 .8c.8 2 2.3 3.5 4.3 4.3l.8-1c.6-.8 1.4-1.1 2.4-.5l3 2c1 1 1 2 0 3l-1 1c-1.5 1.5-5 .5-8.5-3S8.5 13.5 10 12z" fill="#0f4474"/></svg>
        <svg viewBox="0 0 34 34" aria-hidden="true"><circle cx="17" cy="17" r="16" fill="#d98a2b"/><path d="M11 9c1-1 2-1 3 0l2 3c.6 1 .3 1.8-.5 2.4l-1 .8c.8 2 2.3 3.5 4.3 4.3l.8-1c.6-.8 1.4-1.1 2.4-.5l3 2c1 1 1 2 0 3l-1 1c-1.5 1.5-5 .5-8.5-3S8.5 13.5 10 12z" fill="#0f4474"/></svg>
        <svg viewBox="0 0 34 34" aria-hidden="true"><circle cx="17" cy="17" r="16" fill="#d98a2b"/><rect x="9" y="11" width="16" height="12" rx="1.5" fill="#0f4474"/><path d="M9.5 12l7.5 6 7.5-6" stroke="#d98a2b" stroke-width="1.5" fill="none"/></svg>
        <svg viewBox="0 0 34 34" aria-hidden="true"><circle cx="17" cy="17" r="16" fill="#d98a2b"/><circle cx="17" cy="17" r="8" fill="none" stroke="#0f4474" stroke-width="2"/><ellipse cx="17" cy="17" rx="3.5" ry="8" fill="none" stroke="#0f4474" stroke-width="1.6"/><path d="M9 17h16" stroke="#0f4474" stroke-width="1.6"/></svg>
      </div>
      <div class="phones">(931) 555-0148<span class="sep">|</span>(629) 555-0173</div>
      <div class="email">harborlineautoxq@mailnest.example</div>
      <div class="web">www.harborlineautoxq.net</div>
    </div>
  </div>
</body>
</html>
```